Lantern Petals Website v.1 - attract floral shop franchisees

I need a simple information website for my new business. We are a franchisor of flower shops. The overall purpose of the website is to promote the company and the service, especially to potential franchisees and retailers. Only about 4 pages are required including homepage, About, For Supermarkets, For Franchisees, and Contact. No special functions are required except the site will have two separate inquiry forms that must be filled out online and submitted via automated email. Similarly, an email form should be linked from the Contact page. I have a logo and business cards designed by ArtMingle, and I would like the site to have a consistent color scheme and style. The key to design will be to express the joy and love associated with flowers and floral bouquets.
IMPORTANT - I will be exporting the website design to Wordpress CMS in a site hosted by HostNimbus. For smooth integration into WordPress hosted by HostNimbus, the designer should build the site using a WordPress-friendly format. Ideally, they should use HTML, CSS, and PHP. Creating a custom theme or using a page builder that exports to WordPress-compatible files is best. This ensures the site can be easily imported and managed within WordPress.

Target Market(s)

Potential franchisees (existing florists or creative types who might like to own a floral business) and supermarkets who might want us to run their floral department

Industry/Entity Type

Floral retailing

Requirements
Must have
• A brand theme that is beautiful, consistent throughout and builds on the logo design
Nice to have
• Show gender and ethnic diversity in customers and florists. Pictures of happy florists (for franchisees) and pictures of amazing floral department displays (for supermarkets)

```html
<!DOCTYPE html>
<html lang="en">
<head>
<meta charset="utf-8">
<title>Lantern Petals</title>
<link href="https://fonts.googleapis.com/css2?family=Alex+Brush&family=Montserrat:wght@400;500;600;700&display=swap" rel="stylesheet">
<style>
:root{
  --gold:#f2b234;
  --gold-deep:#e9a211;
  --green:#0b8f3c;
  --green-dark:#087a32;
  --ink:#2b2b2b;
  --mist:#eef3f4;
  --white:#ffffff;
}
*{box-sizing:border-box;margin:0;padding:0}
html,body{width:1200px;height:3163px;overflow:hidden}
body{font-family:'Montserrat',sans-serif;color:var(--ink);background:var(--white);position:relative}
.script{font-family:'Alex Brush',cursive;font-weight:400}
.abs{position:absolute}
.btn{position:absolute;display:flex;align-items:center;justify-content:center;font-weight:700;font-size:16px;letter-spacing:.3px;border-radius:3px;text-transform:uppercase}
.btn-green{background:var(--green);color:var(--white)}
.btn-white{background:var(--white);color:var(--green)}
.btn-gold{background:var(--gold-deep);color:var(--white)}

/* hero */
.hero{position:absolute;left:0;top:0;width:1200px;height:760px}
.hero svg{position:absolute;left:0;top:0}
.brand{position:absolute;left:112px;top:28px;display:flex;align-items:center;gap:12px;color:var(--white);font-weight:600;font-size:30px}
.brand .dot{width:52px;height:52px;border:3px solid var(--white);border-radius:50%}
.nav{position:absolute;top:46px;left:489px;font-size:15.5px;font-weight:600;color:var(--white)}
.nav span{position:absolute;white-space:nowrap}
.hero-copy{position:absolute;left:110px;top:200px;color:var(--white)}
.hero-copy .welcome{font-size:35px;font-weight:700;letter-spacing:1px;text-shadow:2px 2px 4px rgba(0,0,0,.25)}
.hero-copy .name{font-family:'Alex Brush',cursive;font-size:92px;color:var(--green);line-height:.9;text-shadow:2px 2px 4px rgba(0,0,0,.2)}
.hero-copy .petals{font-size:62px;font-weight:500;letter-spacing:1px;line-height:1.1;text-shadow:2px 2px 4px rgba(0,0,0,.25)}

/* about */
.about-mark{position:absolute;left:155px;top:870px;width:292px;height:362px}
.about-title{position:absolute;left:595px;top:800px;font-size:66px;color:var(--green)}
.body-text{font-size:15.5px;line-height:28.4px}
.about-text{position:absolute;left:599px;top:888px;width:490px}

/* supermarkets */
.market{position:absolute;left:0;top:1330px;width:1200px;height:630px;background:var(--green);overflow:hidden}
.market-title{position:absolute;left:110px;top:55px;font-size:68px;color:var(--white)}
.market-sub{position:absolute;left:113px;top:145px;font-size:29px;font-weight:600;color:var(--gold)}
.market-list{position:absolute;left:111px;top:205px;width:480px;color:var(--white);list-style:none}

/* franchisees */
.fran{position:absolute;left:0;top:1960px;width:1200px;height:500px;background:var(--mist);overflow:hidden}
.fran-title{position:absolute;left:0;width:1200px;top:45px;text-align:center;font-size:66px;color:var(--gold-deep)}
.fran-text{position:absolute;left:175px;top:148px;width:850px;text-align:center}
.fran-floor{position:absolute;left:0;top:270px;width:1200px;height:230px}

/* contact */
.touch-title{position:absolute;left:0;width:1200px;top:2510px;text-align:center;font-size:70px;color:#151515}

/* footer */
.footer{position:absolute;left:0;top:2745px;width:1200px;height:418px;background:linear-gradient(180deg,#eeae1e,#e7aa23)}
.foot-title{position:absolute;font-size:52px;color:var(--white)}
.foot-links{position:absolute;left:113px;top:150px;list-style:none;color:var(--white);font-size:17px;line-height:31px}
.foot-brand{position:absolute;left:500px;top:60px;width:230px;display:flex;flex-direction:column;align-items:center;gap:14px;color:var(--green);font-weight:700;font-size:24px}
.foot-brand .ring{width:120px;height:120px;border:5px solid var(--green);border-radius:50%}
.socials{position:absolute;left:497px;top:305px;display:flex;gap:11px}
.socials span{width:33px;height:33px;border-radius:50%;background:var(--white);border:2px solid #555}
.contact-row{position:absolute;left:793px;display:flex;align-items:center;gap:20px;color:var(--white);font-size:17px}
.contact-row .ic{width:32px;height:32px;border-radius:50%;background:var(--white);display:flex;align-items:center;justify-content:center}
.foot-rule{position:absolute;left:112px;top:353px;width:976px;height:1px;background:#7b6a3a}
.copyright{position:absolute;left:0;width:1200px;top:384px;text-align:center;color:#6b4a06;font-size:14.5px;font-weight:500;letter-spacing:.6px}
</style>
</head>
<body>

<header class="hero">
  <svg width="1200" height="760" viewBox="0 0 1200 760">
    <defs>
      <linearGradient id="heroPhoto" x1="0" y1="0" x2="1" y2="1">
        <stop offset="0" stop-color="#f3bb45"/>
        <stop offset=".35" stop-color="#eeb13a"/>
        <stop offset=".7" stop-color="#e9a92f"/>
        <stop offset="1" stop-color="#f1b640"/>
      </linearGradient>
      <radialGradient id="bouquet" cx=".55" cy=".4" r=".6">
        <stop offset="0" stop-color="#e94d86"/>
        <stop offset=".22" stop-color="#f0d13a"/>
        <stop offset=".42" stop-color="#6f9a3c"/>
        <stop offset=".62" stop-color="#c8d7b0"/>
        <stop offset=".8" stop-color="#fbfbf7"/>
        <stop offset="1" stop-color="#ffffff"/>
      </radialGradient>
    </defs>
    <path role="img" aria-label="Florist arranging flowers in a shop, tinted gold" fill="url(#heroPhoto)" d="M0,0H1200V165C1010,160 860,230 720,380C580,560 380,680 0,680Z"/>
    <path fill="var(--green)" d="M0,702C260,720 470,640 612,478C520,620 330,735 0,748Z"/>
    <circle role="img" aria-label="Colourful bouquet of roses, gerberas and lilies" cx="985" cy="458" r="290" fill="url(#bouquet)" stroke="var(--gold-deep)" stroke-width="7"/>
  </svg>
  <div class="brand"><span class="dot"></span>Lantern Petals</div>
  <nav class="nav">
    <span style="left:0">Home</span>
    <span style="left:91px">About Us</span>
    <span style="left:207px">For Supermarkets</span>
    <span style="left:392px">For Franchisees</span>
    <span style="left:567px">Contact</span>
  </nav>
  <div class="hero-copy">
    <div class="welcome">WELCOME TO</div>
    <div class="name">Lantern</div>
    <div class="petals">PETALS</div>
  </div>
  <div class="btn btn-green" style="left:111px;top:422px;width:157px;height:43px">Order Now</div>
</header>

<section>
  <svg class="about-mark" viewBox="0 0 292 362">
    <circle cx="146" cy="210" r="143" fill="none" stroke="var(--gold-deep)" stroke-width="7"/>
    <text x="146" y="218" text-anchor="middle" font-family="Montserrat, sans-serif" font-weight="700" font-size="26" fill="var(--green)">Lantern Petals</text>
  </svg>
  <h2 class="about-title script">About Us</h2>
  <p class="about-text body-text">Fresh flowers convey beauty and love, and in our view should become something every person regularly enjoys.&nbsp; Lantern Petals is an entrepreneurial company created to make top quality fresh flowers and professionally-designed bouquets accessible to every consumer at affordable prices.<br>Professional florists typically sell the finest quality stems, design the most beautiful bouquets and provide the finest customer service, but their costs – of floral products, retail spaces, labor and marketing – force them to pass high prices along to customers.</p>
  <div class="btn btn-green" style="left:599px;top:1202px;width:158px;height:43px">Read More</div>
</section>

<section class="market">
  <svg class="abs" style="left:0;top:0" width="1200" height="630" viewBox="0 0 1200 630">
    <defs>
      <linearGradient id="florist" x1="0" y1="0" x2=".6" y2="1">
        <stop offset="0" stop-color="#f4f4f1"/>
        <stop offset=".45" stop-color="#e2ddd4"/>
        <stop offset=".75" stop-color="#d6bf45"/>
        <stop offset="1" stop-color="#4a63b8"/>
      </linearGradient>
    </defs>
    <path fill="var(--white)" d="M952,0H1200V428C1120,428 1040,380 960,290C880,190 860,70 952,0Z"/>
    <circle role="img" aria-label="Smiling florist arranging a yellow and blue bouquet" cx="855" cy="315" r="233" fill="url(#florist)"/>
  </svg>
  <h2 class="market-title script">For Supermarkets</h2>
  <div class="market-sub">Opportunity for Supermarkets</div>
  <ul class="market-list body-text">
    <li>Enhance floral revenue streams with efficient assortments and new offerings</li>
    <li>Reduce the costs of operating a floral department</li>
    <li>Improve the quality, useful life and merchandising of floral products</li>
    <li>Provide attentive customer service, including semi-custom bouquets, by professional florist staff</li>
    <li>Maintain a beautiful, fresh and well-stocked environment</li>
    <li>Increase sales and profits</li>
    <li>Enhance the entire customer shopping environment</li>
  </ul>
  <div class="btn btn-white" style="left:111px;top:517px;width:158px;height:43px">Read More</div>
</section>

<section class="fran">
  <svg class="fran-floor" viewBox="0 0 1200 230" preserveAspectRatio="none" role="img" aria-label="Scattered roses and hellebore flowers with green leaves">
    <defs>
      <linearGradient id="floor" x1="0" y1="0" x2="0" y2="1">
        <stop offset="0" stop-color="#eef3f4" stop-opacity="0"/>
        <stop offset=".45" stop-color="#e3ead6"/>
        <stop offset=".8" stop-color="#c9d89f"/>
        <stop offset="1" stop-color="#e9b7a8"/>
      </linearGradient>
    </defs>
    <rect width="1200" height="230" fill="url(#floor)"/>
  </svg>
  <h2 class="fran-title script">For Franchisees</h2>
  <p class="fran-text body-text">Lantern Petals brings the best of professional florists and supermarkets together for the benefit of consumers.&nbsp; It supports a national network of owner-operator franchisees, who in many cases are multi-site professional florists, with comprehensive services to enhance franchise profitability.&nbsp; Lantern Petals works with some of the country’s largest and most progressive supermarkets to provide franchisee ownership and operation of their strategically important floral departments.</p>
  <div class="btn btn-gold" style="left:521px;top:337px;width:158px;height:43px">Read More</div>
</section>

<section>
  <h2 class="touch-title script">Get In Touch</h2>
  <div class="btn btn-green" style="left:177px;top:2634px;width:354px;height:43px;font-size:15.5px">New Florist Franchise Inquiry</div>
  <div class="btn btn-gold" style="left:583px;top:2634px;width:440px;height:43px;font-size:15.5px">Professional Florist Franchise Inquiry</div>
</section>

<footer class="footer">
  <h3 class="foot-title script" style="left:110px;top:50px">About Company</h3>
  <ul class="foot-links">
    <li>Home</li><li>About Us</li><li>For Supermarkets</li><li>For Franchisees</li><li>Contact</li>
  </ul>
  <div class="foot-brand"><span class="ring"></span>Lantern Petals</div>
  <div class="socials" aria-label="Social media links">
    <span></span><span></span><span></span><span></span><span></span>
  </div>
  <h3 class="foot-title script" style="left:790px;top:50px">Contact Us</h3>
  <div class="contact-row" style="top:160px"><span class="ic"><svg width="18" height="18" viewBox="0 0 24 24"><path d="M6.6 10.8a15 15 0 006.6 6.6l2.2-2.2a1 1 0 011-.25 11 11 0 003.6.6 1 1 0 011 1V20a1 1 0 01-1 1A17 17 0 013 4a1 1 0 011-1h3.5a1 1 0 011 1 11 11 0 00.6 3.6 1 1 0 01-.25 1z" fill="none" stroke="#444" stroke-width="1.6"/></svg></span>+1 (555) 014 2290</div>
  <div class="contact-row" style="top:220px"><span class="ic"><svg width="18" height="14" viewBox="0 0 18 14"><rect x="1" y="1" width="16" height="12" fill="none" stroke="#444" stroke-width="1.4"/><path d="M1 1l8 7 8-7" fill="none" stroke="#444" stroke-width="1.4"/></svg></span>info@lantern-petals.example</div>
  <div class="contact-row" style="top:280px"><span class="ic"><svg width="16" height="20" viewBox="0 0 16 20"><path d="M8 19s-6-7-6-11a6 6 0 0112 0c0 4-6 11-6 11z" fill="none" stroke="#444" stroke-width="1.5"/><circle cx="8" cy="8" r="2.2" fill="none" stroke="#444" stroke-width="1.5"/></svg></span>Maple Harbor City</div>
  <div class="foot-rule"></div>
  <div class="copyright">© COPYRIGHTS 2024 LANTERN-PETALS. ALL RIGHTS RESERVED.</div>
</footer>

</body>
</html>
```